Business Card Design

We need a business card designed for our new company. Prefer a black card with white logo & writing.

Contact Information for Business Card

Ted Galloway, address: 7-4812 Fernhollow Road, Abbotsford, BC, V3K 8R2, Office Phone: 604-712-3390, Cell: 604-947-2164, Email: ted@resinworkshub.ca

Colors

Designer to choose only greyscale colors for use in the design.

```html
<!DOCTYPE html>
<html lang="en">
<head>
<meta charset="utf-8">
<title>Resinworks Hub — Business Card</title>
<link href="https://fonts.googleapis.com/css2?family=Montserrat:wght@400;700;800&display=swap" rel="stylesheet">
<style>
  :root {
    --backdrop: #262626;
    --card: #000000;
    --ink: #ffffff;
  }
  html, body {
    margin: 0;
    width: 1200px;
    height: 900px;
    overflow: hidden;
    background: var(--backdrop);
    font-family: "Montserrat", Arial, sans-serif;
    color: var(--ink);
  }
  .card {
    position: absolute;
    left: 341px;
    width: 518px;
    height: 296px;
    background: var(--card);
  }
  .card--front { top: 141px; }
  .card--back { top: 463px; }

  .brand {
    position: absolute;
    left: 0;
    right: 0;
    display: flex;
    align-items: center;
    justify-content: center;
    gap: 10px;
    font-weight: 800;
    letter-spacing: 0.5px;
    text-transform: uppercase;
    color: var(--ink);
  }
  .brand__dot {
    border: 2px solid var(--ink);
    border-radius: 50%;
    box-sizing: border-box;
  }
  .card--front .brand { top: 78px; font-size: 26px; }
  .card--front .brand__dot { width: 20px; height: 20px; }
  .card--back .brand { top: 124px; font-size: 40px; gap: 14px; }
  .card--back .brand__dot { width: 30px; height: 30px; border-width: 3px; }

  .divider {
    position: absolute;
    left: 0;
    top: 0;
  }
  .holder-name {
    position: absolute;
    right: 27px;
    top: 196px;
    margin: 0;
    font-size: 17px;
    font-weight: 700;
    letter-spacing: 0.3px;
    text-transform: uppercase;
  }
  .contact-list {
    position: absolute;
    left: 27px;
    top: 201px;
    margin: 0;
    padding: 0;
    list-style: none;
    font-size: 13.5px;
    line-height: 18px;
  }
  .contact-list li {
    display: flex;
    align-items: center;
    gap: 6px;
  }
  .contact-list svg {
    width: 11px;
    height: 11px;
    flex: none;
  }
  .address {
    position: absolute;
    right: 27px;
    top: 236px;
    margin: 0;
    font-style: normal;
    font-size: 13.5px;
    line-height: 18px;
    text-align: right;
  }
</style>
</head>
<body>

<section class="card card--front" aria-label="Business card front">
  <div class="brand"><span class="brand__dot"></span>Resinworks Hub</div>

  <svg class="divider" width="518" height="296" viewBox="0 0 518 296" aria-hidden="true">
    <g fill="none" stroke="#fff" stroke-width="1.4">
      <line x1="27" y1="188" x2="491" y2="188"/>
      <polyline points="301,188 367,225 491,225"/>
    </g>
  </svg>

  <h1 class="holder-name">Ted Galloway</h1>

  <ul class="contact-list">
    <li>
      <svg viewBox="0 0 12 12" aria-hidden="true"><path fill="#fff" d="M2.4 0.6l1.8 2.2-1 1.2c.6 1.5 1.8 2.7 3.3 3.3l1.2-1 2.2 1.8-.9 1.9C5.2 10.2 1.3 6.1.6 1.5z"/></svg>
      604-712-3390
    </li>
    <li>
      <svg viewBox="0 0 12 12" aria-hidden="true"><rect x="3" y="0.6" width="6" height="10.8" rx="1" fill="none" stroke="#fff" stroke-width="1.2"/><circle cx="6" cy="9.4" r="0.7" fill="#fff"/></svg>
      604-947-2164
    </li>
    <li>
      <svg viewBox="0 0 12 12" aria-hidden="true"><rect x="0.5" y="2.5" width="11" height="7.5" fill="#fff"/><polyline points="0.5,2.5 6,6.8 11.5,2.5" fill="none" stroke="#000" stroke-width="1"/></svg>
      ted@resinworkshub.ca
    </li>
    <li>
      <svg viewBox="0 0 12 12" aria-hidden="true"><g fill="none" stroke="#fff" stroke-width="0.9"><circle cx="6" cy="6" r="5.2"/><ellipse cx="6" cy="6" rx="2.3" ry="5.2"/><line x1="0.8" y1="6" x2="11.2" y2="6"/><line x1="1.6" y1="3.4" x2="10.4" y2="3.4"/><line x1="1.6" y1="8.6" x2="10.4" y2="8.6"/></g></svg>
      resinworkshub.ca
    </li>
  </ul>

  <address class="address">
    7-4812 Fernhollow Road<br>
    Abbotsford, BC, V3K 8R2
  </address>
</section>

<section class="card card--back" aria-label="Business card back">
  <div class="brand"><span class="brand__dot"></span>Resinworks Hub</div>
</section>

</body>
</html>
```